Travel Agency Website - Simple General

Need a 7 page simple design that is pretty repetitive. Need to be able to load quickly that is SEO optimized. Trying to give ideas on what they can do, be personal as we are local, but at the same time come across as professional and get information easily with little burden.

- Landing Page
- Brimwell Vacations Page
- Family Trips
- Road Trips from Texas
- Other Destinations
- About Us Page
- Contact Us Page

Target Market(s)

Families

Coding

Coded - Design and coding required

Number of Pages Required

5+ page

Colors

Designer to choose colors to be used in the design.

Requirements
Must have
• Like it to flow easily with our logo. Use that for colors, etc.

```html
<!DOCTYPE html>
<html lang="en">
<head>
<meta charset="utf-8">
<title>About Page Designs – Hum Along Roamers</title>
<link href="https://fonts.googleapis.com/css2?family=Outfit:wght@300;400;500;600;700&display=swap" rel="stylesheet">
<style>
:root{
  --board:#a3a3a3;
  --teal:#1d5a5f;
  --teal-soft:#4d7f82;
  --gold:#c8964a;
  --paper:#f1f3ef;
  --paper-warm:#f3f1e9;
  --line:#dcdfdb;
  --white:#ffffff;
}
*{box-sizing:border-box;margin:0;padding:0}
html,body{width:1200px;height:1151px;overflow:hidden;background:var(--board)}
body{font-family:'Outfit',sans-serif;color:var(--teal)}
.board{position:absolute;left:0;top:0;width:1960px;height:1879px;transform:scale(0.61224);transform-origin:0 0;background:var(--board)}
.board-title{position:absolute;left:0;width:1960px;top:70px;text-align:center;font-size:104px;font-weight:600;color:var(--white);letter-spacing:1px;line-height:1.1}
.page{position:absolute;width:820px;overflow:hidden;background:linear-gradient(180deg,#e8f0ee 0%,var(--paper) 35%,var(--paper-warm) 100%)}
.page-left{left:100px;top:260px;height:1201px}
.page-right-a{left:975px;top:260px;height:688px}
.page-right-b{left:975px;top:1017px;height:688px}
.abs{position:absolute}
.contact-bar{position:absolute;left:380px;top:0;width:380px;height:26px;background:var(--teal);border-radius:0 0 8px 8px;display:flex;align-items:center;justify-content:center;gap:18px;color:var(--white);font-size:9px}
.contact-bar span{display:flex;align-items:center;gap:6px}
.contact-bar svg{width:15px;height:15px}
.brand{position:absolute;left:62px;top:34px;display:flex;align-items:center;gap:6px;font-size:15px;font-weight:600;color:var(--teal);width:150px;line-height:1.1}
.brand-dot{width:16px;height:16px;border-radius:50%;background:var(--gold);flex:none}
.nav{position:absolute;left:222px;top:48px;display:flex;align-items:center;gap:15px;font-size:10px;color:var(--teal)}
.nav .active{border-bottom:1.5px solid var(--gold);padding-bottom:5px;margin-top:7px}
.nav .home{width:10px;height:10px}
.btn-contact{position:absolute;left:663px;top:43px;width:94px;height:25px;border-radius:13px;background:var(--gold);color:var(--white);font-size:9px;display:flex;align-items:center;justify-content:space-between;padding:0 4px 0 17px}
.btn-contact i{width:17px;height:17px;border-radius:50%;border:1px solid rgba(255,255,255,.7);display:flex;align-items:center;justify-content:center;font-style:normal;font-size:9px}
.eyebrow{font-size:13px;font-weight:300;letter-spacing:.5px;color:var(--teal)}
.heading{font-weight:600;color:var(--teal);line-height:1.13;letter-spacing:.5px}
.sparkle{color:var(--gold);font-size:14px;position:absolute;font-weight:400}
.lead{font-size:15px;font-weight:500;line-height:20px;color:var(--teal)}
.body-text{font-size:10.8px;line-height:17.4px;font-weight:300;color:var(--teal)}
.body-text p+p{margin-top:12px}
.checks{list-style:none;font-size:10.5px;font-weight:400;letter-spacing:.3px}
.checks li{display:flex;align-items:center;gap:8px;height:20px}
.checks svg{width:10px;height:10px}
.photo{position:absolute;border-radius:3px}
.ph-cliffs{background:linear-gradient(170deg,#8fbde6 0%,#5f7f54 35%,#6f9a5a 55%,#d9c8a8 80%,#e8dcc4 100%)}
.ph-family{background:linear-gradient(180deg,#9ccbef 0%,#bcdcf2 45%,#d9747a 70%,#5b9ac9 100%)}
.ph-castle{background:linear-gradient(180deg,#4f8fd6 0%,#9bc1ea 40%,#c7a7c4 70%,#3e6ea8 100%)}
.ph-sunset{background:linear-gradient(180deg,#f1c27d 0%,#d99a5b 35%,#a8866a 60%,#d8c7b2 100%)}
.frame{position:absolute;border:4px solid var(--white);box-shadow:0 0 0 1.5px #c9b48e;border-radius:46% 40% 44% 38% / 30% 34% 30% 36%}
.section-title{position:absolute;font-size:20px;font-weight:600;letter-spacing:.5px}
.card{position:absolute;top:550px;width:134px;height:159px;background:var(--white);border:1px solid var(--line);border-radius:3px;text-align:center;padding:22px 8px 0}
.card svg{width:34px;height:34px}
.card h3{font-size:10.5px;font-weight:500;margin-top:12px;color:#222}
.card p{font-size:8.5px;line-height:12.5px;font-weight:300;color:#333;margin-top:4px}
.card::after{content:"";position:absolute;left:42px;right:42px;bottom:0;height:1.5px;background:var(--gold)}
.block{position:absolute;background:var(--teal)}
.footer{position:absolute;left:0;bottom:0;width:820px;height:51px;background:var(--white);font-size:8.5px;color:#444}
.footer .copy{position:absolute;left:0;width:800px;text-align:center;top:20px}
.footer .social{position:absolute;top:13px;display:flex;gap:6px}
.footer .social b{display:block;width:15px;height:15px;border-radius:50%;background:var(--teal)}
</style>
</head>
<body>
<div class="board">
  <h1 class="board-title">ABOUT PAGE DESIGNS</h1>

  <!-- Layout A: split hero, reasons, story -->
  <section class="page page-left">
    <div class="contact-bar">
      <span><svg viewBox="0 0 16 16"><circle cx="8" cy="8" r="8" fill="#fff"/><rect x="4" y="5" width="8" height="6" fill="none" stroke="#1d5a5f" stroke-width="1"/><path d="M4 5l4 3 4-3" fill="none" stroke="#1d5a5f"/></svg>HumAlongRoamers@mailbox.com</span>
      <span><svg viewBox="0 0 16 16"><circle cx="8" cy="8" r="8" fill="#fff"/><path d="M5 4.5c0 4 2.5 6.5 6.5 6.5l.5-1.8-2-1-1 1c-1-.5-1.7-1.2-2.2-2.2l1-1-1-2z" fill="#1d5a5f"/></svg>Phone Number (555) 014 2870</span>
    </div>
    <div class="brand"><span class="brand-dot"></span>Hum Along Roamers</div>
    <nav class="nav">
      <svg class="home" viewBox="0 0 10 10"><path d="M1 5L5 1l4 4v4H6V6H4v3H1z" fill="#c8964a"/></svg>
      <span>Brimwell Vacations</span><span>Family Trips</span><span>Texas Road Trips</span><span>Other Destinations</span><span class="active">About Us</span>
    </nav>
    <div class="btn-contact">Contact Us<i>↗</i></div>

    <div class="abs eyebrow" style="left:74px;top:150px">ABOUT US</div>
    <h2 class="abs heading" style="left:74px;top:166px;font-size:32px">HUM ALONG<br>ROAMERS<span class="sparkle" style="left:200px;top:-8px">✦</span></h2>
    <div class="abs lead" style="left:76px;top:250px;width:300px">Creating unforgettable travel experiences, one journey at a time.</div>
    <div class="abs body-text" style="left:76px;top:303px;width:322px">At Hum Along Roamers, we believe travel should be exciting, stress-free, and filled with unforgettable memories. Whether you're dreaming of a magical Brimwell vacation, planning a fun family getaway, or exploring scenic road trip destinations, we're here to help make every step of your journey simple and enjoyable.</div>
    <div class="frame ph-cliffs" style="left:470px;top:95px;width:310px;height:305px" role="img" aria-label="Couple walking hand in hand on a tropical beach below limestone cliffs"></div>
    <div class="frame ph-sunset" style="left:405px;top:265px;width:205px;height:190px" role="img" aria-label="Couple relaxing on a boat deck at sunset"></div>

    <h2 class="section-title" style="left:0;width:820px;text-align:center;top:498px">WHY TRAVEL WITH US<span class="sparkle" style="left:520px;top:-10px">✦</span></h2>

    <div class="card" style="left:58px"><svg viewBox="0 0 34 34" fill="none" stroke="#1d5a5f" stroke-width="1.3"><circle cx="17" cy="14" r="10"/><path d="M17 9l1.5 3 3.3.4-2.4 2.3.6 3.3-3-1.6-3 1.6.6-3.3-2.4-2.3 3.3-.4z" stroke="#c8964a"/><path d="M11 22l-3 9 4-2 2 3 2-7M23 22l3 9-4-2-2 3-2-7"/></svg><h3>Expert Guidance</h3><p>Years of experience and first-hand destination knowledge.</p></div>
    <div class="card" style="left:199px"><svg viewBox="0 0 34 34" fill="none" stroke="#1d5a5f" stroke-width="1.3"><path d="M17 29S4 21 4 12a6.5 6.5 0 0113-2 6.5 6.5 0 0113 2c0 9-13 17-13 17z"/><path d="M24 6l1 2 2 1-2 1-1 2-1-2-2-1 2-1z" fill="#c8964a" stroke="none"/></svg><h3>Personalized Trips</h3><p>Every trip is customized to match your style, needs, and budget.</p></div>
    <div class="card" style="left:340px"><svg viewBox="0 0 34 34" fill="none" stroke="#1d5a5f" stroke-width="1.3"><circle cx="17" cy="17" r="13"/><path d="M17 9v8l5 4"/></svg><h3>Save Time &amp; Stress</h3><p>We handle the details so you can focus on making memories.</p></div>
    <div class="card" style="left:480px"><svg viewBox="0 0 34 34" fill="none" stroke="#1d5a5f" stroke-width="1.3"><circle cx="20" cy="9" r="6" stroke="#c8964a"/><path d="M20 6v6" stroke="#c8964a"/><path d="M3 22h5v8H3zM8 23h8l3 2h7l4-3v2l-6 5H8"/></svg><h3>Best Value</h3><p>Top recommendations and insider tips to get the best value.</p></div>
    <div class="card" style="left:620px"><svg viewBox="0 0 34 34" fill="none" stroke="#1d5a5f" stroke-width="1.3"><circle cx="17" cy="16" r="7"/><path d="M7 17a10 10 0 0120 0M6 15h3v6H6zM25 15h3v6h-3zM27 21c0 4-4 6-8 6"/></svg><h3>Ongoing Support</h3><p>We're with you every step of the way—before, during, and after your trip.</p></div>

    <div class="block" style="left:52px;top:773px;width:92px;height:85px"></div>
    <div class="block" style="left:322px;top:1000px;width:92px;height:87px"></div>
    <div class="photo ph-cliffs" style="left:59px;top:779px;width:172px;height:300px" role="img" aria-label="Couple in sun hats walking along a tropical beach"></div>
    <div class="photo ph-family" style="left:238px;top:779px;width:172px;height:156px" role="img" aria-label="Happy family with arms spread on a seaside trip"></div>
    <div class="photo ph-castle" style="left:238px;top:942px;width:172px;height:137px" role="img" aria-label="Theme park castle towers under a blue sky"></div>

    <h2 class="abs heading" style="left:443px;top:780px;font-size:27px">OUR STORY<span class="sparkle" style="left:150px;top:-8px">✦</span></h2>
    <div class="abs body-text" style="left:443px;top:824px;width:345px">
      <p>At Hum Along Roamers, we believe travel should be exciting, stress-free, and filled with unforgettable memories. Whether you're dreaming of a magical Brimwell vacation, planning a fun family getaway, or exploring scenic road trip destinations, we're here to help make every step of your journey simple and enjoyable.</p>
      <p>We specialize in personalized travel planning tailored to your unique needs, preferences, and budget. From destination recommendations and itinerary planning to travel tips and support, our goal is to help you create experiences that bring families closer and adventures to life.</p>
    </div>
    <ul class="abs checks" style="left:448px;top:1008px">
      <li><svg viewBox="0 0 10 10"><path d="M1 5l3 3 5-6" fill="none" stroke="#c8964a" stroke-width="1.4"/></svg>Personalized Travel Planning</li>
      <li><svg viewBox="0 0 10 10"><path d="M1 5l3 3 5-6" fill="none" stroke="#c8964a" stroke-width="1.4"/></svg>Brimwell Vacations &amp; Family Getaways</li>
      <li><svg viewBox="0 0 10 10"><path d="M1 5l3 3 5-6" fill="none" stroke="#c8964a" stroke-width="1.4"/></svg>Texas Road Trips &amp; Unique Destinations</li>
      <li><svg viewBox="0 0 10 10"><path d="M1 5l3 3 5-6" fill="none" stroke="#c8964a" stroke-width="1.4"/></svg>Stress-Free Travel Support</li>
    </ul>
    <footer class="footer"><div class="copy">© 2026 Hum Along Roamers. All Right Reserved</div><div class="social" style="left:681px"><b></b><b></b></div></footer>
  </section>

  <!-- Layout B: centered title, photo grid -->
  <section class="page page-right-a">
    <div class="contact-bar">
      <span><svg viewBox="0 0 16 16"><circle cx="8" cy="8" r="8" fill="#fff"/><rect x="4" y="5" width="8" height="6" fill="none" stroke="#1d5a5f"/><path d="M4 5l4 3 4-3" fill="none" stroke="#1d5a5f"/></svg>HumAlongRoamers@mailbox.com</span>
      <span><svg viewBox="0 0 16 16"><circle cx="8" cy="8" r="8" fill="#fff"/><path d="M5 4.5c0 4 2.5 6.5 6.5 6.5l.5-1.8-2-1-1 1c-1-.5-1.7-1.2-2.2-2.2l1-1-1-2z" fill="#1d5a5f"/></svg>Phone Number (555) 014 2870</span>
    </div>
    <div class="brand"><span class="brand-dot"></span>Hum Along Roamers</div>
    <nav class="nav">
      <svg class="home" viewBox="0 0 10 10"><path d="M1 5L5 1l4 4v4H6V6H4v3H1z" fill="#c8964a"/></svg>
      <span>Brimwell Vacations</span><span>Family Trips</span><span>Texas Road Trips</span><span>Other Destinations</span><span class="active">About Us</span>
    </nav>
    <div class="btn-contact">Contact Us<i>↗</i></div>

    <div class="abs eyebrow" style="left:0;width:820px;text-align:center;top:116px">WHO WE ARE</div>
    <h2 class="abs heading" style="left:0;width:820px;text-align:center;top:134px;font-size:32px">ABOUT HUM ALONG<br>ROAMERS<span class="sparkle" style="left:560px;top:-8px">✦</span></h2>
    <div class="photo ph-cliffs" style="left:56px;top:250px;width:175px;height:306px" role="img" aria-label="Couple in sun hats walking along a tropical beach"></div>
    <div class="photo ph-family" style="left:239px;top:250px;width:175px;height:158px" role="img" aria-label="Happy family with arms spread on a seaside trip"></div>
    <div class="photo ph-castle" style="left:239px;top:416px;width:175px;height:140px" role="img" aria-label="Theme park castle towers under a blue sky"></div>
    <div class="abs lead" style="left:443px;top:247px;width:320px">Creating unforgettable travel experiences, one journey at a time.</div>
    <div class="abs body-text" style="left:443px;top:298px;width:345px">
      <p>At Hum Along Roamers, we believe travel should be exciting, stress-free, and filled with unforgettable memories. Whether you're dreaming of a magical Brimwell vacation, planning a fun family getaway, or exploring scenic road trip destinations, we're here to help make every step of your journey simple and enjoyable.</p>
      <p>We specialize in personalized travel planning tailored to your unique needs, preferences, and budget. From destination recommendations and itinerary planning to travel tips and support, our goal is to help you create experiences that bring families closer and adventures to life.</p>
    </div>
    <ul class="abs checks" style="left:448px;top:482px">
      <li><svg viewBox="0 0 10 10"><path d="M1 5l3 3 5-6" fill="none" stroke="#c8964a" stroke-width="1.4"/></svg>Personalized Travel Planning</li>
      <li><svg viewBox="0 0 10 10"><path d="M1 5l3 3 5-6" fill="none" stroke="#c8964a" stroke-width="1.4"/></svg>Brimwell Vacations &amp; Family Getaways</li>
      <li><svg viewBox="0 0 10 10"><path d="M1 5l3 3 5-6" fill="none" stroke="#c8964a" stroke-width="1.4"/></svg>Texas Road Trips &amp; Unique Destinations</li>
      <li><svg viewBox="0 0 10 10"><path d="M1 5l3 3 5-6" fill="none" stroke="#c8964a" stroke-width="1.4"/></svg>Stress-Free Travel Support</li>
    </ul>
    <footer class="footer"><div class="copy">© 2026 Hum Along Roamers. All Right Reserved</div><div class="social" style="left:679px"><b></b><b></b></div></footer>
  </section>

  <!-- Layout C: centered title, framed collage -->
  <section class="page page-right-b">
    <div class="contact-bar">
      <span><svg viewBox="0 0 16 16"><circle cx="8" cy="8" r="8" fill="#fff"/><rect x="4" y="5" width="8" height="6" fill="none" stroke="#1d5a5f"/><path d="M4 5l4 3 4-3" fill="none" stroke="#1d5a5f"/></svg>HumAlongRoamers@mailbox.com</span>
      <span><svg viewBox="0 0 16 16"><circle cx="8" cy="8" r="8" fill="#fff"/><path d="M5 4.5c0 4 2.5 6.5 6.5 6.5l.5-1.8-2-1-1 1c-1-.5-1.7-1.2-2.2-2.2l1-1-1-2z" fill="#1d5a5f"/></svg>Phone Number (555) 014 2870</span>
    </div>
    <div class="brand"><span class="brand-dot"></span>Hum Along Roamers</div>
    <nav class="nav">
      <svg class="home" viewBox="0 0 10 10"><path d="M1 5L5 1l4 4v4H6V6H4v3H1z" fill="#c8964a"/></svg>
      <span>Brimwell Vacations</span><span>Family Trips</span><span>Texas Road Trips</span><span>Other Destinations</span><span class="active">About Us</span>
    </nav>
    <div class="btn-contact">Contact Us<i>↗</i></div>

    <div class="abs eyebrow" style="left:0;width:820px;text-align:center;top:110px">WHO WE ARE</div>
    <h2 class="abs heading" style="left:0;width:820px;text-align:center;top:128px;font-size:32px">ABOUT HUM ALONG<br>ROAMERS<span class="sparkle" style="left:560px;top:-8px">✦</span></h2>
    <div class="frame ph-cliffs" style="left:45px;top:228px;width:305px;height:285px" role="img" aria-label="Couple walking hand in hand on a tropical beach below limestone cliffs"></div>
    <div class="frame ph-sunset" style="left:212px;top:365px;width:203px;height:222px" role="img" aria-label="Couple relaxing on a boat deck at sunset"></div>
    <div class="abs lead" style="left:444px;top:246px;width:320px">Creating unforgettable travel experiences, one journey at a time.</div>
    <div class="abs body-text" style="left:444px;top:297px;width:345px">
      <p>At Hum Along Roamers, we believe travel should be exciting, stress-free, and filled with unforgettable memories. Whether you're dreaming of a magical Brimwell vacation, planning a fun family getaway, or exploring scenic road trip destinations, we're here to help make every step of your journey simple and enjoyable.</p>
      <p>We specialize in personalized travel planning tailored to your unique needs, preferences, and budget. From destination recommendations and itinerary planning to travel tips and support, our goal is to help you create experiences that bring families closer and adventures to life.</p>
    </div>
    <ul class="abs checks" style="left:449px;top:486px">
      <li><svg viewBox="0 0 10 10"><path d="M1 5l3 3 5-6" fill="none" stroke="#c8964a" stroke-width="1.4"/></svg>Personalized Travel Planning</li>
      <li><svg viewBox="0 0 10 10"><path d="M1 5l3 3 5-6" fill="none" stroke="#c8964a" stroke-width="1.4"/></svg>Brimwell Vacations &amp; Family Getaways</li>
      <li><svg viewBox="0 0 10 10"><path d="M1 5l3 3 5-6" fill="none" stroke="#c8964a" stroke-width="1.4"/></svg>Texas Road Trips &amp; Unique Destinations</li>
      <li><svg viewBox="0 0 10 10"><path d="M1 5l3 3 5-6" fill="none" stroke="#c8964a" stroke-width="1.4"/></svg>Stress-Free Travel Support</li>
    </ul>
    <footer class="footer"><div class="copy">© 2026 Hum Along Roamers. All Right Reserved</div><div class="social" style="left:679px"><b></b><b></b></div></footer>
  </section>
</div>
</body>
</html>
```